I have a logo and need to design the business card and stationery.
Updates

The uploaded logo image named as GREYMARSH CONTRACTS which is to be replaced to GREYMARSH CONTRACTS. Kindly add below details and submit the designs- Company name- Greymarsh Engineering Contracts LLP Name & Post- Kelvan Joshi (Designated Partner) Address- Block No.317, Wing C, Tulvo Trade Court, Manek Pural Road, Ruparel Industrial Estate, Goregaon(E), Mumbai - 400 063 Contact- +91 97415 60382 Email- kelvanjoshi@mailbrook.example Website- www.greymarshcontracts.example Contact for Letterhead- +91-22-28754193

Hi Tovin Rahul, We are liking your Design #28860835. We have suggested some changes which are mentioned in feedback. Kindly revert with it asap to finalize this design.

Colors

Designer to choose colors to be used in the design.

```html
<!DOCTYPE html>
<html lang="en">
<head>
<meta charset="utf-8">
<title>Greymarsh Contracts – Business Card</title>
<link href="https://fonts.googleapis.com/css2?family=Montserrat:wght@300;400;600;700&display=swap" rel="stylesheet">
<style>
  :root {
    --backdrop: #141414;
    --card: #232323;
    --ink: #ffffff;
    --ink-soft: #d9d9d9;
    --emboss: #3a3a3a;
    --rule: #e6e6e6;
  }
  * { margin: 0; padding: 0; box-sizing: border-box; }
  html, body {
    width: 1200px; height: 900px; overflow: hidden;
    background: var(--backdrop);
    font-family: "Montserrat", Arial, sans-serif;
    color: var(--ink);
  }
  .sheet {
    width: 1200px; height: 900px;
    display: flex; flex-direction: column;
    align-items: center; justify-content: center; gap: 40px;
  }
  .card {
    position: relative;
    width: 700px; height: 400px;
    background: var(--card);
    box-shadow: 0 14px 40px rgba(0,0,0,.6);
  }
  /* Front */
  .holder { position: absolute; left: 48px; top: 52px; }
  .holder-name { font-size: 27px; font-weight: 600; letter-spacing: 1px; }
  .holder-title { font-size: 15px; font-weight: 300; letter-spacing: 1px; color: var(--ink-soft); margin-top: 2px; }
  .divider { position: absolute; left: 48px; right: 150px; top: 142px; height: 1.5px; background: var(--rule); }
  .contacts { position: absolute; left: 48px; top: 164px; list-style: none; }
  .contacts li {
    display: flex; align-items: center; gap: 10px;
    font-size: 16px; font-weight: 400; line-height: 30px;
    white-space: nowrap;
  }
  .contacts svg { width: 13px; height: 13px; flex: none; }
  .brand {
    position: absolute; right: 48px; top: 52px;
    display: flex; align-items: center; gap: 14px;
  }
  .brand-mark { width: 54px; height: 54px; border: 6px solid var(--ink); }
  .brand-name {
    font-size: 24px; font-weight: 700; letter-spacing: 2px; line-height: 1.15;
    color: var(--ink);
  }
  .address {
    position: absolute; right: 48px; bottom: 36px; width: 300px;
    font-size: 14px; font-weight: 400; line-height: 21px; text-align: left;
    color: var(--ink-soft);
  }
  .address-company { font-weight: 600; color: var(--ink); }
  /* Back */
  .card-back { display: flex; align-items: center; justify-content: center; }
  .card-back .brand { position: static; gap: 22px; }
  .card-back .brand-mark { width: 96px; height: 96px; border-width: 10px; border-color: var(--emboss); }
  .card-back .brand-name { font-size: 44px; color: var(--emboss); letter-spacing: 4px; }
</style>
</head>
<body>
<main class="sheet">
  <section class="card card-front">
    <div class="holder">
      <p class="holder-name">KELVAN JOSHI</p>
      <p class="holder-title">DESIGNATED PARTNER</p>
    </div>
    <div class="divider"></div>
    <ul class="contacts">
      <li>
        <svg viewBox="0 0 24 24" fill="#fff"><path d="M6.6 10.8a15.1 15.1 0 0 0 6.6 6.6l2.2-2.2c.3-.3.7-.4 1-.2 1.1.4 2.3.6 3.6.6.6 0 1 .4 1 1V20c0 .6-.4 1-1 1A17 17 0 0 1 3 4c0-.6.4-1 1-1h3.5c.6 0 1 .4 1 1 0 1.3.2 2.5.6 3.6.1.3 0 .7-.2 1z"/></svg>
        +91 97415 60382
      </li>
      <li>
        <svg viewBox="0 0 24 24" fill="none" stroke="#fff" stroke-width="2"><rect x="2" y="5" width="20" height="14"/><path d="M2 5l10 8 10-8"/></svg>
        kelvanjoshi@mailbrook.example
      </li>
      <li>
        <svg viewBox="0 0 24 24" fill="none" stroke="#fff" stroke-width="2"><circle cx="12" cy="12" r="10"/><path d="M2 12h20M12 2c3 3 3 17 0 20M12 2c-3 3-3 17 0 20"/></svg>
        www.greymarshcontracts.example
      </li>
    </ul>
    <div class="brand">
      <div class="brand-name">GREYMARSH<br>CONTRACTS</div>
      <div class="brand-mark"></div>
    </div>
    <p class="address">
      <span class="address-company">Greymarsh Engineering Contracts LLP</span><br>
      Block No.317, Wing C, Tulvo Trade Court, Manek Pural Road, Ruparel Industrial Estate, Goregaon(E), Mumbai - 400 063
    </p>
  </section>

  <section class="card card-back">
    <div class="brand">
      <div class="brand-name">GREYMARSH<br>CONTRACTS</div>
      <div class="brand-mark"></div>
    </div>
  </section>
</main>
</body>
</html>
```